Sunscreen Package Design Modern SPF 50

Update current package design to a more modern design target women 16-40 Do not make it playful. SOLANE COVE is home to movie stars and high income business people PalmSprings is one of the most desired vacation areas in the world. The sun shines 350 days a year. World class Tennis and Golf tournaments are held every year with the worlds top players attending these tournaments

Target Market(s)

Women

Industry/Entity Type

Skin Protection

Font styles to use
Sans Serif

Requirements
Must have
• The words SOLANE COVE and KORIVELL

```html
<!DOCTYPE html>
<html lang="en">
<head>
<meta charset="utf-8">
<title>Solane Cove Aftersun — Colour Range</title>
<link href="https://fonts.googleapis.com/css2?family=Montserrat:wght@400;500&display=swap" rel="stylesheet">
<style>
  :root {
    --backdrop: #e4e4e4;
    --ink: #ffffff;
    --sage: #8a9580;     --sage-cap: #3f4a32;
    --sand: #b08d68;     --sand-cap: #4d3a2e;
    --slate: #71879a;    --slate-cap: #34424e;
    --mauve: #8e7c86;    --mauve-cap: #3e3438;
    --clay: #b27665;     --clay-cap: #7a4634;
    --lagoon: #7e9f9c;   --lagoon-cap: #2f4a48;
  }
  * { margin: 0; padding: 0; box-sizing: border-box; }
  html, body { width: 1200px; height: 912px; overflow: hidden; }
  body { background: var(--backdrop); position: relative; font-family: "Montserrat", sans-serif; }

  .tube { position: absolute; width: 184px; height: 415px; }
  .tube-shape { position: absolute; inset: 0; }
  .tube-body { fill: var(--tone); }
  .tube-crimp { fill: #000; opacity: .06; }
  .tube-cap { fill: var(--cap); }
  .tube-cap-notch { fill: none; stroke: #000; stroke-opacity: .25; stroke-width: 1.2; }

  .tube--sage   { --tone: var(--sage);   --cap: var(--sage-cap); }
  .tube--sand   { --tone: var(--sand);   --cap: var(--sand-cap); }
  .tube--slate  { --tone: var(--slate);  --cap: var(--slate-cap); }
  .tube--mauve  { --tone: var(--mauve);  --cap: var(--mauve-cap); }
  .tube--clay   { --tone: var(--clay);   --cap: var(--clay-cap); }
  .tube--lagoon { --tone: var(--lagoon); --cap: var(--lagoon-cap); }

  .label { position: absolute; left: 0; width: 184px; text-align: center; color: var(--ink); }
  .name-dot {
    position: absolute; top: 66px; left: 86px; width: 12px; height: 12px;
    border-radius: 50%; background: var(--ink); opacity: .85;
  }
  .brand-name {
    position: absolute; top: 100px; font-weight: 500;
    font-size: 19px; line-height: 24px; letter-spacing: 3px;
  }
  .brand-name span { display: block; }
  .maker { position: absolute; top: 154px; font-size: 6.5px; letter-spacing: 2.4px; font-weight: 500; }
  .divider { position: absolute; top: 182px; left: 91.5px; width: 1px; height: 61px; background: var(--ink); opacity: .85; }
  .product { position: absolute; top: 260px; font-size: 9px; letter-spacing: 3px; font-weight: 500; }
  .benefits { position: absolute; top: 284px; font-size: 5.6px; letter-spacing: .2px; }
  .ingredients { position: absolute; top: 297px; font-size: 5.6px; line-height: 11px; letter-spacing: .2px; }
  .volume { position: absolute; top: 333px; font-size: 6px; letter-spacing: .3px; }
</style>
</head>
<body>

<div class="tube tube--sage" style="left:236px; top:52px;">
  <svg class="tube-shape" viewBox="0 0 184 415" aria-hidden="true">
    <path class="tube-body" d="M0 0 H184 L176 290 C172 330 160 355 142 365 H42 C24 355 12 330 8 290 Z"/>
    <rect class="tube-crimp" x="0" y="0" width="184" height="14"/>
    <path class="tube-cap" d="M42 365 H142 V405 Q142 415 132 415 H52 Q42 415 42 405 Z"/>
    <rect class="tube-cap-notch" x="70" y="384" width="44" height="20"/>
  </svg>
  <div class="name-dot"></div>
  <div class="label brand-name"><span>SOLANE</span><span>COVE</span></div>
  <div class="label maker">KORIVELL</div>
  <div class="divider"></div>
  <div class="label product">AFTERSUN</div>
  <div class="label benefits">HYDRATE / SOOTHE / RESTORE</div>
  <div class="label ingredients">WITH ALOE, HYALURONATE ACID<br>CUCUMBER &amp; JOJOBA</div>
  <div class="label volume">3 FL OZ / 88 mL</div>
</div>

<div class="tube tube--sand" style="left:508px; top:52px;">
  <svg class="tube-shape" viewBox="0 0 184 415" aria-hidden="true">
    <path class="tube-body" d="M0 0 H184 L176 290 C172 330 160 355 142 365 H42 C24 355 12 330 8 290 Z"/>
    <rect class="tube-crimp" x="0" y="0" width="184" height="14"/>
    <path class="tube-cap" d="M42 365 H142 V405 Q142 415 132 415 H52 Q42 415 42 405 Z"/>
    <rect class="tube-cap-notch" x="70" y="384" width="44" height="20"/>
  </svg>
  <div class="name-dot"></div>
  <div class="label brand-name"><span>SOLANE</span><span>COVE</span></div>
  <div class="label maker">KORIVELL</div>
  <div class="divider"></div>
  <div class="label product">AFTERSUN</div>
  <div class="label benefits">HYDRATE / SOOTHE / RESTORE</div>
  <div class="label ingredients">WITH ALOE, HYALURONATE ACID<br>CUCUMBER &amp; JOJOBA</div>
  <div class="label volume">3 FL OZ / 88 mL</div>
</div>

<div class="tube tube--slate" style="left:781px; top:52px;">
  <svg class="tube-shape" viewBox="0 0 184 415" aria-hidden="true">
    <path class="tube-body" d="M0 0 H184 L176 290 C172 330 160 355 142 365 H42 C24 355 12 330 8 290 Z"/>
    <rect class="tube-crimp" x="0" y="0" width="184" height="14"/>
    <path class="tube-cap" d="M42 365 H142 V405 Q142 415 132 415 H52 Q42 415 42 405 Z"/>
    <rect class="tube-cap-notch" x="70" y="384" width="44" height="20"/>
  </svg>
  <div class="name-dot"></div>
  <div class="label brand-name"><span>SOLANE</span><span>COVE</span></div>
  <div class="label maker">KORIVELL</div>
  <div class="divider"></div>
  <div class="label product">AFTERSUN</div>
  <div class="label benefits">HYDRATE / SOOTHE / RESTORE</div>
  <div class="label ingredients">WITH ALOE, HYALURONATE ACID<br>CUCUMBER &amp; JOJOBA</div>
  <div class="label volume">3 FL OZ / 88 mL</div>
</div>

<div class="tube tube--mauve" style="left:236px; top:488px;">
  <svg class="tube-shape" viewBox="0 0 184 415" aria-hidden="true">
    <path class="tube-body" d="M0 0 H184 L176 290 C172 330 160 355 142 365 H42 C24 355 12 330 8 290 Z"/>
    <rect class="tube-crimp" x="0" y="0" width="184" height="14"/>
    <path class="tube-cap" d="M42 365 H142 V405 Q142 415 132 415 H52 Q42 415 42 405 Z"/>
    <rect class="tube-cap-notch" x="70" y="384" width="44" height="20"/>
  </svg>
  <div class="name-dot"></div>
  <div class="label brand-name"><span>SOLANE</span><span>COVE</span></div>
  <div class="label maker">KORIVELL</div>
  <div class="divider"></div>
  <div class="label product">AFTERSUN</div>
  <div class="label benefits">HYDRATE / SOOTHE / RESTORE</div>
  <div class="label ingredients">WITH ALOE, HYALURONATE ACID<br>CUCUMBER &amp; JOJOBA</div>
  <div class="label volume">3 FL OZ / 88 mL</div>
</div>

<div class="tube tube--clay" style="left:508px; top:488px;">
  <svg class="tube-shape" viewBox="0 0 184 415" aria-hidden="true">
    <path class="tube-body" d="M0 0 H184 L176 290 C172 330 160 355 142 365 H42 C24 355 12 330 8 290 Z"/>
    <rect class="tube-crimp" x="0" y="0" width="184" height="14"/>
    <path class="tube-cap" d="M42 365 H142 V405 Q142 415 132 415 H52 Q42 415 42 405 Z"/>
    <rect class="tube-cap-notch" x="70" y="384" width="44" height="20"/>
  </svg>
  <div class="name-dot"></div>
  <div class="label brand-name"><span>SOLANE</span><span>COVE</span></div>
  <div class="label maker">KORIVELL</div>
  <div class="divider"></div>
  <div class="label product">AFTERSUN</div>
  <div class="label benefits">HYDRATE / SOOTHE / RESTORE</div>
  <div class="label ingredients">WITH ALOE, HYALURONATE ACID<br>CUCUMBER &amp; JOJOBA</div>
  <div class="label volume">3 FL OZ / 88 mL</div>
</div>

<div class="tube tube--lagoon" style="left:781px; top:488px;">
  <svg class="tube-shape" viewBox="0 0 184 415" aria-hidden="true">
    <path class="tube-body" d="M0 0 H184 L176 290 C172 330 160 355 142 365 H42 C24 355 12 330 8 290 Z"/>
    <rect class="tube-crimp" x="0" y="0" width="184" height="14"/>
    <path class="tube-cap" d="M42 365 H142 V405 Q142 415 132 415 H52 Q42 415 42 405 Z"/>
    <rect class="tube-cap-notch" x="70" y="384" width="44" height="20"/>
  </svg>
  <div class="name-dot"></div>
  <div class="label brand-name"><span>SOLANE</span><span>COVE</span></div>
  <div class="label maker">KORIVELL</div>
  <div class="divider"></div>
  <div class="label product">AFTERSUN</div>
  <div class="label benefits">HYDRATE / SOOTHE / RESTORE</div>
  <div class="label ingredients">WITH ALOE, HYALURONATE ACID<br>CUCUMBER &amp; JOJOBA</div>
  <div class="label volume">3 FL OZ / 88 mL</div>
</div>

</body>
</html>
```